Hi Designers,

I will need 4 web pages designed. The web page looks like an App (if you click on the logo, or the icon on an iPad, it will take you to the website), but it is still a webpage.

Please check the attachment on this brief to understand what specific pages I need to be designed.

A .PSD (straight-up PhotoShop image) as final deliverable is fine, as long as you give us the exact “web color numbers”.

The design is for desktop and iPad but in a single unified web application, NOT separate web app and (native) iPad app.

Details:

Brightwater Policy Partners is developing a browser-based application for use on any mobile device or desktop. The app will be used by corporations to communicate with their employees regarding legal, regulatory and company requirements for conducting business. The app is known as “Harbor Guidance Portal.” When the user clicks on the icon for Harbor Guidance Portal, they will enter a site full of information that a company deems necessary for the employee to do his/her job. There are several content sections within the site, including a login page, training, policies, forms, news feeds and blogs.

The application has been built using Microsoft .NET, and fully supports CSS-type skinning; it uses traditional page layouts. We are seeking a product logo concept (image), a master application/desktop icon (image), as well as a full color scheme/theme/skin design for all areas of the application (header area, body text, menu bar, etc.) in the form of a CSS. The look should be clean, crisp and professional; nothing cartoony or whimsical. It should be easy to read and “airy”.

We have sketched prototypes for the basic application page layout that we can send as a next step of the process.
Updates

Screen shots have been uploaded to this project.  Please use them to guide your design.

Dear designers,

I apologize for the delay in providing feedback. My partners and I will provide feedback in a few days. Thank you for your patience.

Industry/Entity Type

Business

Font styles to use
Other font styles liked:
• see font on screen shots when uploaded

```html
<!DOCTYPE html>
<html lang="en">
<head>
<meta charset="utf-8">
<title>Novaline — Sign in</title>
<link rel="stylesheet" href="https://fonts.googleapis.com/css2?family=Source+Sans+3:ital,wght@0,400;0,600;0,700;1,400&display=swap">
<style>
  :root {
    --page-navy: #032a4f;
    --panel-top: #e2e2e2;
    --panel-bottom: #ffffff;
    --label-grey: #555a60;
    --field-border: #c6c6c6;
    --field-fill: #ffffff;
    --button-top: #3c86c4;
    --button-bottom: #135a98;
    --button-edge: #0e4878;
    --brand-dark: #0d2c4e;
    --brand-accent: #1a7bc0;
    --logo-text: #e6ecf2;
    --white: #ffffff;
  }
  * { box-sizing: border-box; margin: 0; padding: 0; }
  html, body {
    width: 1200px; height: 723px; overflow: hidden;
    background: var(--page-navy);
    font-family: "Source Sans 3", "Myriad Pro", Arial, sans-serif;
  }
  .screen { position: relative; width: 1200px; height: 723px; }

  .product-mark {
    position: absolute; left: 521px; top: 150px;
    display: flex; align-items: center; gap: 18px;
  }
  .product-mark__dot {
    width: 50px; height: 50px; border-radius: 50%;
    background: radial-gradient(circle at 40% 40%, #3fb2d8, #1d5f8a);
  }
  .product-mark__name {
    color: var(--logo-text); font-size: 19px; font-weight: 400; letter-spacing: .2px;
  }

  .login-panel {
    position: absolute; left: 358px; top: 230px; width: 484px; height: 268px;
    border-radius: 4px;
    background: linear-gradient(to bottom, var(--panel-top), var(--panel-bottom) 85%);
  }
  .field-label {
    position: absolute; right: calc(484px - 126px); width: 100px; text-align: right;
    color: var(--label-grey); font-size: 11px;
  }
  .field-label--user { top: 55px; }
  .field-label--pass { top: 105px; }
  .field-input {
    position: absolute; left: 138px; width: 312px; height: 31px;
    border: 1px solid var(--field-border); border-radius: 4px;
    background: var(--field-fill);
  }
  .field-input--user { top: 44px; }
  .field-input--pass { top: 96px; }

  .remember {
    position: absolute; left: 81px; top: 163px;
    display: flex; align-items: center; gap: 6px;
    color: var(--label-grey); font-size: 11px;
  }
  .remember__box {
    width: 9px; height: 9px; border: 1px solid #9a9a9a;
    background: linear-gradient(#ffffff, #dcdcdc);
  }
  .forgot-link {
    position: absolute; left: 219px; top: 163px;
    color: var(--label-grey); font-size: 11px; font-style: italic;
    text-decoration: underline;
  }
  .sign-in-button {
    position: absolute; left: 345px; top: 148px; width: 104px; height: 36px;
    border: 1px solid var(--button-edge); border-radius: 3px;
    background: linear-gradient(var(--button-top), var(--button-bottom));
    color: var(--white); font-size: 14px; font-weight: 700;
    display: flex; align-items: center; justify-content: center;
  }

  .portal-mark {
    position: absolute; left: 124px; top: 211px;
    display: flex; align-items: center; gap: 6px;
  }
  .portal-mark__dot {
    width: 30px; height: 30px; border-radius: 50%; background: var(--brand-accent);
  }
  .portal-mark__name {
    color: var(--brand-dark); font-size: 11.5px; font-weight: 700; letter-spacing: .1px;
  }

  .copyright {
    position: absolute; left: 0; width: 1200px; top: 518px; text-align: center;
    color: var(--white); font-size: 9.5px; font-weight: 600;
  }
  .version-tag {
    position: absolute; left: 905px; top: 517px;
    color: var(--white); font-size: 10px;
  }
</style>
</head>
<body>
<main class="screen">
  <div class="product-mark">
    <span class="product-mark__dot"></span>
    <span class="product-mark__name">Novaline</span>
  </div>

  <section class="login-panel">
    <span class="field-label field-label--user">User name :</span>
    <div class="field-input field-input--user"></div>
    <span class="field-label field-label--pass">Password :</span>
    <div class="field-input field-input--pass"></div>

    <label class="remember"><span class="remember__box"></span>Keep me signed in</label>
    <span class="forgot-link">Forgot password?</span>
    <div class="sign-in-button">SIGN IN</div>

    <div class="portal-mark">
      <span class="portal-mark__dot"></span>
      <span class="portal-mark__name">HARBOR GUIDANCE PORTAL</span>
    </div>
  </section>

  <p class="copyright">Copyrights © 2013. Harbor Guidance Portal. All rights reserved.</p>
  <span class="version-tag">C8</span>
</main>
</body>
</html>
```